design a construction company business card

Design business card around our logo. Card must have all the typical info: name, title, address, phone, email, business name, etc. Somewhere on the card I would like to see our motto "Built on integrity... Inspired by commitment." Consider adding a splash of bright orange to the card to complement the blues and silvers/grays in the logo. We are open to metallic inks, textures, etc. We would like to see options on both light and dark backgrounds. The font in the logo is Euro Technic Extended Regular.

```html
<!DOCTYPE html>
<html lang="en">
<head>
<meta charset="utf-8">
<title>Halden Builders – Business Card</title>
<link href="https://fonts.googleapis.com/css2?family=Source+Sans+3:wght@400;600;700&display=swap" rel="stylesheet">
<style>
  :root {
    --sheet-light: #e8e9eb;
    --sheet-dark: #cfd0d2;
    --sheet-edge: #3a3a3a;
    --card-white: #ffffff;
    --brand-blue: #1b6fc0;
    --band-deep: #283a8e;
    --band-bright: #1e7bc8;
    --rule-grey: #8a8b8e;
    --text-grey: #5a5b5e;
    --back-grey: #808184;
  }
  html, body {
    margin: 0;
    padding: 0;
    width: 800px;
    height: 1200px;
    overflow: hidden;
  }
  .sheet {
    position: relative;
    width: 800px;
    height: 1200px;
    box-sizing: border-box;
    border: 1px solid var(--sheet-edge);
    background: radial-gradient(ellipse at 50% 50%, var(--sheet-light) 0%, var(--sheet-dark) 75%);
    font-family: "Source Sans 3", sans-serif;
  }
  .card {
    position: absolute;
    width: 504px;
    height: 288px;
  }
  .card-front {
    left: 148px;
    top: 174px;
    background: var(--card-white);
  }
  .card-back {
    left: 156px;
    top: 703px;
    background: var(--back-grey);
  }
  .wordmark {
    position: absolute;
    left: 0;
    right: 0;
    text-align: center;
    font-weight: 700;
    letter-spacing: 2px;
    line-height: 1.1;
  }
  .wordmark-front {
    top: 58px;
    color: var(--brand-blue);
    font-size: 30px;
  }
  .wordmark-back {
    top: 118px;
    color: var(--card-white);
    font-size: 30px;
  }
  .wordmark .mark-square {
    display: inline-block;
    width: 18px;
    height: 18px;
    margin-right: 10px;
    background: currentColor;
    vertical-align: 2px;
  }
  .wordmark .sub {
    display: block;
    font-size: 30px;
  }
  .holder {
    position: absolute;
    right: 256px;
    top: 163px;
    text-align: right;
  }
  .holder-name {
    color: var(--brand-blue);
    font-size: 23px;
    font-weight: 600;
    line-height: 1.1;
  }
  .holder-title {
    color: var(--text-grey);
    font-size: 13.5px;
    margin-top: 2px;
  }
  .divider {
    position: absolute;
    left: 262px;
    top: 142px;
    width: 1px;
    height: 84px;
    background: var(--text-grey);
  }
  .contacts {
    position: absolute;
    left: 281px;
    top: 149px;
    margin: 0;
    padding: 0;
    list-style: none;
    color: var(--text-grey);
    font-size: 13.5px;
    line-height: 17px;
  }
  .contacts li {
    display: flex;
    align-items: center;
    gap: 6px;
  }
  .contacts svg {
    width: 9px;
    height: 9px;
    fill: var(--brand-blue);
    flex: none;
  }
  .rule {
    position: absolute;
    left: 0;
    width: 504px;
    height: 3px;
    background: var(--rule-grey);
  }
  .rule-top { top: 241px; }
  .rule-bottom { top: 285px; }
  .address-band {
    position: absolute;
    left: 0;
    top: 247px;
    width: 504px;
    height: 34px;
    background: linear-gradient(90deg, var(--band-deep) 0%, var(--band-bright) 100%);
    color: var(--card-white);
    font-size: 13.5px;
    line-height: 34px;
    text-align: center;
  }
</style>
</head>
<body>
  <main class="sheet">
    <section class="card card-front" aria-label="Business card front">
      <div class="wordmark wordmark-front"><span class="mark-square"></span>HALDEN<span class="sub">BUILDERS, INC.</span></div>

      <div class="holder">
        <div class="holder-name">Daniel Marsh</div>
        <div class="holder-title">Managing Member</div>
      </div>

      <div class="divider"></div>

      <ul class="contacts">
        <li>
          <svg viewBox="0 0 10 10" aria-hidden="true"><path d="M2 0.5 L4 2.8 L3 4 Q4.2 6 6 7 L7.2 6 L9.5 8 L8.3 9.5 Q4.5 9.5 0.5 1.7 Z"/></svg>
          (555) 214-7730
        </li>
        <li>
          <svg viewBox="0 0 10 10" aria-hidden="true"><path d="M2.5 0 H7.5 V10 H2.5 Z M3.5 1 V8 H6.5 V1 Z"/></svg>
          (555) 309-4418
        </li>
        <li>
          <svg viewBox="0 0 10 10" aria-hidden="true"><path d="M0 2 H10 V8.5 H0 Z M0.8 2.6 L5 5.6 L9.2 2.6 V3.4 L5 6.4 L0.8 3.4 Z" fill-rule="evenodd"/></svg>
          daniel@haldenbuild.com
        </li>
        <li>
          <svg viewBox="0 0 10 10" aria-hidden="true"><path d="M5 0 A5 5 0 1 0 5.01 0 Z M5 1 A4 4 0 1 1 4.99 1 Z M4.5 0.5 H5.5 V9.5 H4.5 Z M0.5 4.5 H9.5 V5.5 H0.5 Z" fill-rule="evenodd"/></svg>
          www.haldenbuild.com
        </li>
      </ul>

      <div class="rule rule-top"></div>
      <div class="address-band">2280 Granite Row, Fairview, CA 95800</div>
      <div class="rule rule-bottom"></div>
    </section>

    <section class="card card-back" aria-label="Business card back">
      <div class="wordmark wordmark-back"><span class="mark-square"></span>HALDEN<span class="sub">BUILDERS, INC.</span></div>
    </section>
  </main>
</body>
</html>
```